Laboratory and geotechnical service provider needs Word template

We require a new Word Template for our business. We are looking for a modern, business-like format. We typically generate reports such as management plans, business plans, method statements, technical reports. These reports cover generally between 5 and 30 pages, but sometimes up to 500 pages including the appendices.

Lab reports have their own formats and are not parts of this scope.

Target Market(s)

We report to Clients such as construction industry contractors, governmental departments and engineering consultants.

Industry/Entity Type

Technical Service

Colors

Designer to choose colors to be used in the design.

Requirements
Must have
• The report needs a fancy cover page with a title field, subtitle, project field, client name field, reference number field. Photo/graphics as background on cover. Second page needs a revision table for document control. Table of contents up to 2 levels. Appendices to be part of TOC. Report first page with custom headings for body text, titles, subtitles, headings 1, 2, 3, etc. Include a table with caption, figure with caption, bullet list, numbered list. Appendix page. Please use fonts consistently, choose a common, but professional, modern font.
Nice to have
• We traditionally use black and yellow as company colours. Please visit our company page www.brennixtesting.com.
Should not have
• The two attached word documents is what we use now for your information, we are looking for something better!

```html
<!DOCTYPE html>
<html lang="en">
<head>
<meta charset="utf-8">
<title>Brennix Testing Co. WLL – Cover page versions</title>
<link rel="stylesheet" href="https://fonts.googleapis.com/css2?family=Ubuntu:wght@400;500;700&display=swap">
<style>
  :root {
    --brand-yellow: #fecb1a;
    --page-yellow: #fdc90b;
    --ink: #000000;
    --paper: #ffffff;
    --muted: #555555;
    --photo-grey-light: #c9c9c9;
    --photo-grey-dark: #6f6f6f;
    --photo-yellow-light: #f3d24a;
    --photo-yellow-dark: #8a6d10;
  }
  * { box-sizing: border-box; margin: 0; padding: 0; }
  html, body { width: 1200px; height: 1108px; overflow: hidden; }
  body {
    background: var(--brand-yellow);
    font-family: "Ubuntu", sans-serif;
    color: var(--ink);
    position: relative;
  }

  /* Header */
  .brand-header { position: absolute; left: 85px; top: 26px; display: flex; align-items: center; }
  .brand-mark {
    width: 93px; height: 71px; border: 1.5px solid var(--ink);
    display: flex; align-items: center; justify-content: center;
    font-weight: 700; font-size: 15px; letter-spacing: 0.5px;
  }
  .brand-name { margin-left: 14px; font-size: 25px; font-weight: 400; }

  /* Cover pages */
  .cover {
    position: absolute; width: 298px; height: 422px;
    background: var(--paper); overflow: hidden;
    box-shadow: 0 1px 3px rgba(0,0,0,0.25);
  }
  .cover.is-yellow { background: var(--paper); }
  .cover .yellow-field { position: absolute; left: 0; top: 0; width: 298px; height: 263px; background: var(--page-yellow); }
  .col-1 { left: 85px; } .col-2 { left: 452px; } .col-3 { left: 819px; }
  .row-1 { top: 127px; } .row-2 { top: 618px; }

  .caption {
    position: absolute; width: 298px; text-align: center;
    font-size: 15px; font-weight: 400;
  }
  .caption.row-1 { top: 551px; } .caption.row-2 { top: 1042px; }

  /* Photo placeholders */
  .photo { position: absolute; }
  .photo.site-yellow { background: linear-gradient(180deg, var(--photo-yellow-light), var(--photo-yellow-dark)); }
  .photo.lab-grey { background: linear-gradient(160deg, var(--photo-grey-light), var(--photo-grey-dark)); }
  .photo.lab-light { background: linear-gradient(160deg, #e6e6e6, #7a7a7a); }
  .photo.lab-yellow { background: linear-gradient(160deg, #f5d865, #6e5a14); }
  .photo.site-grey { background: linear-gradient(180deg, #e2e2e2, #7c7c7c); }
  .photo.framed { border: 4px solid var(--ink); }
  .photo.framed-thin { border: 2px solid var(--ink); }

  /* Title band */
  .band { position: absolute; left: 0; top: 263px; width: 298px; height: 37px; background: var(--ink); }
  .band-titles { position: absolute; top: 263px; height: 37px; display: flex; flex-direction: column; justify-content: center; }
  .band-titles.align-right { text-align: right; }
  .doc-title { color: var(--page-yellow); font-size: 14px; font-weight: 500; line-height: 1.15; letter-spacing: 0.2px; }
  .doc-subtitle { color: var(--paper); font-size: 7.5px; font-weight: 500; margin-top: 3px; }
  .band-logo {
    position: absolute; display: flex; align-items: center; justify-content: center;
    color: var(--page-yellow); font-weight: 700; font-size: 10px; letter-spacing: 0.3px;
  }
  .band-logo.on-yellow { color: var(--ink); background: var(--page-yellow); }
  .band-logo.on-black { background: var(--ink); }

  /* Project info */
  .project { position: absolute; left: 23px; top: 308px; width: 260px; }
  .project-title { font-size: 12px; font-weight: 500; }
  .ref-number { font-size: 6.5px; color: var(--muted); margin-top: 4px; letter-spacing: 0.3px; }
  .client-name { font-size: 10px; color: var(--muted); margin-top: 17px; letter-spacing: 0.3px; }
  .contact { list-style: none; margin-top: 13px; }
  .contact li { font-size: 6px; color: #333; display: flex; align-items: center; height: 9px; }
  .contact svg { width: 6px; height: 6px; margin-right: 5px; fill: #333; }
</style>
</head>
<body>

<header class="brand-header">
  <div class="brand-mark">BRENNIX</div>
  <div class="brand-name">Brennix Testing Co. WLL</div>
</header>

<!-- Version 1 -->
<section class="cover col-1 row-1">
  <div class="photo site-yellow" style="left:0;top:0;width:298px;height:128px" role="img" aria-label="Drilling rig on site with city skyline and palm trees, yellow toned"></div>
  <div style="position:absolute;left:0;top:128px;width:298px;height:7px;background:var(--ink)"></div>
  <div class="photo lab-grey" style="left:0;top:135px;width:298px;height:128px" role="img" aria-label="Laboratory technician working at a microscope, grey toned"></div>
  <div class="band" style="width:202px"></div>
  <div class="band-titles align-right" style="left:0;width:198px">
    <div class="doc-title">Document Title</div>
    <div class="doc-subtitle">Document Subtitle</div>
  </div>
  <div class="band-logo on-yellow" style="left:202px;top:263px;width:96px;height:37px">BRENNIX</div>
  <div class="project">
    <div class="project-title">Project Title</div>
    <div class="ref-number">reference number</div>
    <div class="client-name">Clients Name</div>
    <ul class="contact">
      <li><svg viewBox="0 0 6 6"><path d="M0 2h6v1H5v3H1V3H0z"/></svg>+974 4412 0385</li>
      <li><svg viewBox="0 0 6 6"><circle cx="3" cy="3" r="2.5" fill="none" stroke="#333" stroke-width="1"/></svg>info@brennixtesting.com</li>
      <li><svg viewBox="0 0 6 6"><rect x="0" y="1" width="6" height="4"/></svg>www.brennixtesting.com</li>
    </ul>
  </div>
</section>
<div class="caption col-1 row-1">Cover page - version 1</div>

<!-- Version 2 -->
<section class="cover col-2 row-1">
  <div class="photo lab-light" style="left:0;top:0;width:230px;height:300px" role="img" aria-label="Laboratory technician at a microscope with sample tubes, grey toned"></div>
  <div style="position:absolute;left:232px;top:0;width:66px;height:263px;background:var(--page-yellow)"></div>
  <div class="photo site-yellow" style="left:232px;top:100px;width:66px;height:163px" role="img" aria-label="Drilling rig on site, yellow toned"></div>
  <div class="band" style="width:230px;background:rgba(0,0,0,0.85)"></div>
  <div class="band-titles align-right" style="left:0;width:222px">
    <div class="doc-title">Document Title</div>
    <div class="doc-subtitle">Document Subtitle</div>
  </div>
  <div class="band-logo on-black" style="left:233px;top:263px;width:65px;height:37px">BRENNIX</div>
  <div class="project">
    <div class="project-title">Project Title</div>
    <div class="ref-number">reference number</div>
    <div class="client-name">Clients Name</div>
    <ul class="contact">
      <li><svg viewBox="0 0 6 6"><path d="M0 2h6v1H5v3H1V3H0z"/></svg>+974 4412 0385</li>
      <li><svg viewBox="0 0 6 6"><circle cx="3" cy="3" r="2.5" fill="none" stroke="#333" stroke-width="1"/></svg>info@brennixtesting.com</li>
      <li><svg viewBox="0 0 6 6"><rect x="0" y="1" width="6" height="4"/></svg>www.brennixtesting.com</li>
    </ul>
  </div>
</section>
<div class="caption col-2 row-1">Cover page - version 2</div>

<!-- Version 3 -->
<section class="cover col-3 row-1">
  <div class="photo lab-yellow" style="left:0;top:0;width:230px;height:300px" role="img" aria-label="Laboratory technician at a microscope with sample tubes, yellow toned"></div>
  <div class="photo site-grey" style="left:232px;top:0;width:66px;height:263px" role="img" aria-label="Drilling rig on site, grey toned"></div>
  <div class="band" style="width:230px;background:rgba(0,0,0,0.85)"></div>
  <div class="band-titles align-right" style="left:0;width:222px">
    <div class="doc-title">Document Title</div>
    <div class="doc-subtitle">Document Subtitle</div>
  </div>
  <div class="band-logo on-black" style="left:233px;top:263px;width:65px;height:37px">BRENNIX</div>
  <div class="project">
    <div class="project-title">Project Title</div>
    <div class="ref-number">reference number</div>
    <div class="client-name">Clients Name</div>
    <ul class="contact">
      <li><svg viewBox="0 0 6 6"><path d="M0 2h6v1H5v3H1V3H0z"/></svg>+974 4412 0385</li>
      <li><svg viewBox="0 0 6 6"><circle cx="3" cy="3" r="2.5" fill="none" stroke="#333" stroke-width="1"/></svg>info@brennixtesting.com</li>
      <li><svg viewBox="0 0 6 6"><rect x="0" y="1" width="6" height="4"/></svg>www.brennixtesting.com</li>
    </ul>
  </div>
</section>
<div class="caption col-3 row-1">Cover page - version 3</div>

<!-- Version 4 -->
<section class="cover col-1 row-2">
  <div class="yellow-field" style="height:259px"></div>
  <div class="photo site-yellow framed" style="left:176px;top:14px;width:110px;height:110px" role="img" aria-label="Drilling rig on site, yellow toned"></div>
  <div class="photo lab-yellow framed" style="left:176px;top:135px;width:110px;height:110px" role="img" aria-label="Laboratory technician at a microscope, yellow toned"></div>
  <div class="band"></div>
  <div class="band-titles align-right" style="left:0;width:222px">
    <div class="doc-title">Document Title</div>
    <div class="doc-subtitle">Document Subtitle</div>
  </div>
  <div class="band-logo on-black" style="left:226px;top:263px;width:64px;height:37px">BRENNIX</div>
  <div class="project">
    <div class="project-title">Project Title</div>
    <div class="ref-number">reference number</div>
    <div class="client-name">Clients Name</div>
    <ul class="contact">
      <li><svg viewBox="0 0 6 6"><path d="M0 2h6v1H5v3H1V3H0z"/></svg>+974 4412 0385</li>
      <li><svg viewBox="0 0 6 6"><circle cx="3" cy="3" r="2.5" fill="none" stroke="#333" stroke-width="1"/></svg>info@brennixtesting.com</li>
      <li><svg viewBox="0 0 6 6"><rect x="0" y="1" width="6" height="4"/></svg>www.brennixtesting.com</li>
    </ul>
  </div>
</section>
<div class="caption col-1 row-2">Cover page - version 4</div>

<!-- Version 5 -->
<section class="cover col-2 row-2">
  <div class="yellow-field"></div>
  <div class="photo lab-yellow framed-thin" style="left:7px;top:163px;width:92px;height:92px" role="img" aria-label="Laboratory technician at a microscope, yellow toned"></div>
  <div class="photo site-yellow framed-thin" style="left:104px;top:163px;width:92px;height:92px" role="img" aria-label="Drilling rig on site, yellow toned"></div>
  <div class="band-logo on-black" style="left:199px;top:163px;width:93px;height:92px;font-size:15px">BRENNIX</div>
  <div class="band"></div>
  <div class="band-titles" style="left:23px;width:220px">
    <div class="doc-title">Document Title</div>
    <div class="doc-subtitle">Document Subtitle</div>
  </div>
  <div class="project">
    <div class="project-title">Project Title</div>
    <div class="ref-number">reference number</div>
    <div class="client-name">Clients Name</div>
    <ul class="contact">
      <li><svg viewBox="0 0 6 6"><path d="M0 2h6v1H5v3H1V3H0z"/></svg>+974 4412 0385</li>
      <li><svg viewBox="0 0 6 6"><circle cx="3" cy="3" r="2.5" fill="none" stroke="#333" stroke-width="1"/></svg>info@brennixtesting.com</li>
      <li><svg viewBox="0 0 6 6"><rect x="0" y="1" width="6" height="4"/></svg>www.brennixtesting.com</li>
    </ul>
  </div>
</section>
<div class="caption col-2 row-2">Cover page - version 5</div>

<!-- Version 6 -->
<section class="cover col-3 row-2">
  <div class="yellow-field"></div>
  <div class="photo site-yellow" style="left:202px;top:0;width:81px;height:150px" role="img" aria-label="Drilling rig on site, yellow toned"></div>
  <div style="position:absolute;left:202px;top:150px;width:81px;height:2px;background:var(--ink)"></div>
  <div class="photo lab-yellow" style="left:202px;top:152px;width:81px;height:148px" role="img" aria-label="Laboratory technician at a microscope, yellow toned"></div>
  <div style="position:absolute;left:200px;top:0;width:2px;height:263px;background:var(--ink)"></div>
  <div style="position:absolute;left:283px;top:0;width:2px;height:263px;background:var(--ink)"></div>
  <div class="band" style="width:202px"></div>
  <div class="band" style="left:202px;width:81px;background:rgba(0,0,0,0.6)"></div>
  <div class="band" style="left:283px;width:15px"></div>
  <div class="band-titles align-right" style="left:0;width:198px">
    <div class="doc-title">Document Title</div>
    <div class="doc-subtitle">Document Subtitle</div>
  </div>
  <div class="band-logo" style="left:206px;top:263px;width:74px;height:37px">BRENNIX</div>
  <div class="project">
    <div class="project-title">Project Title</div>
    <div class="ref-number">reference number</div>
    <div class="client-name">Clients Name</div>
    <ul class="contact">
      <li><svg viewBox="0 0 6 6"><path d="M0 2h6v1H5v3H1V3H0z"/></svg>+974 4412 0385</li>
      <li><svg viewBox="0 0 6 6"><circle cx="3" cy="3" r="2.5" fill="none" stroke="#333" stroke-width="1"/></svg>info@brennixtesting.com</li>
      <li><svg viewBox="0 0 6 6"><rect x="0" y="1" width="6" height="4"/></svg>www.brennixtesting.com</li>
    </ul>
  </div>
</section>
<div class="caption col-3 row-2">Cover page - version 6</div>

</body>
</html>
```